New Electrical Contractor looking for local work

I have just started working for myself as an Electrical Contractor, based in the eastern suburbs of Melbourne. I want to advertise in the local area so hopefully I can create a client base that is close to home, so I thought a flyer that I could drop in letterboxes could be a good start. Most of my experience has been domestic houses, so ideally this is the work I would like to get more of.

Here is a list of the work I usually do:
Extensions / Renovations
Safety Switch and Switchboard Upgrades
LED Lighting including downlights/light fittings and LED strip light
Re-wires
Maintenance

I have also added a couple of images of LED strip lights and how they can be used in homes. There are a lot more on google images if anyone thinks they could be of use.

These are my details:
Business name - Dirk Malan Electrical
Phone - 0437 218 064
ABN - 41 382 704 916
REC - 58317
Email - malanelectrical@brivomail.net

I will attach my business logo and business card
Updates

Could I please ask for all designs to delete the "(contractors registration number)" text.

Only REC 58317 needs to be displayed.

Thank you kindly

Industry/Entity Type

Business

Requirements
Must have
• My contact details, ie. Name, Phone, email, ABN, REC etc

```html
<!DOCTYPE html>
<html lang="en">
<head>
<meta charset="utf-8">
<title>Dirk Malan Electrical – Flyer</title>
<link href="https://fonts.googleapis.com/css2?family=Alfa+Slab+One&family=Open+Sans:wght@600&family=Tinos:wght@400;700&display=swap" rel="stylesheet">
<style>
  :root {
    --red-deep: #a80019;
    --red-mid: #dc122c;
    --red-glow: #f04656;
    --blue-deep: #0a3fa8;
    --blue-bright: #2f7fe6;
    --blue-light: #8fc4ff;
    --white: #ffffff;
    --ink-shadow: rgba(80, 0, 10, 0.55);
    --frame: rgba(255, 255, 255, 0.85);
  }
  * { margin: 0; padding: 0; box-sizing: border-box; }
  html, body { width: 1200px; height: 899px; overflow: hidden; background: #fff; }
  .flyer {
    position: relative;
    width: 1200px;
    height: 899px;
    overflow: hidden;
    background: radial-gradient(ellipse at 45% 45%, var(--red-glow) 0%, var(--red-mid) 40%, var(--red-deep) 100%);
    color: var(--white);
  }
  .swoosh { position: absolute; inset: 0; width: 1200px; height: 899px; }
  .brand-mark {
    position: absolute; left: 30px; top: 28px;
    width: 120px; height: 120px; border-radius: 50%;
    background: var(--white);
  }
  .brand-name {
    position: absolute; left: 182px; top: 22px;
    font-family: "Alfa Slab One", Georgia, serif;
    font-weight: 400; font-size: 76px; line-height: 1;
    color: var(--white);
    text-shadow: 3px 3px 0 var(--ink-shadow);
    white-space: nowrap;
  }
  .tagline {
    position: absolute; left: 272px; top: 120px;
    font-family: "Open Sans", Arial, sans-serif;
    font-weight: 600; font-size: 40px; line-height: 1;
    color: var(--white);
    white-space: nowrap;
  }
  .gallery { position: absolute; inset: 0; }
  .photo {
    position: absolute;
    border: 2px solid var(--frame);
    box-shadow: 0 3px 8px rgba(60, 0, 8, 0.45);
  }
  .photo-hall    { left: 42px;  top: 190px; width: 375px; height: 134px;
    background: radial-gradient(ellipse at 22% 88%, #5a7cff 0%, transparent 35%),
                radial-gradient(ellipse at 80% 45%, #f2d45a 0%, #8a7a2c 30%, transparent 55%),
                linear-gradient(90deg, #0e1226, #2b3566 45%, #3a3a2a); }
  .photo-kitchen { left: 434px; top: 190px; width: 349px; height: 134px;
    background: radial-gradient(ellipse at 50% 80%, #ffd27a 0%, #c9782a 35%, transparent 70%),
                linear-gradient(180deg, #2a160a, #6e3e18 55%, #a86428); }
  .photo-stairs  { left: 804px; top: 190px; width: 354px; height: 134px;
    background: radial-gradient(ellipse at 65% 55%, #6f8cff 0%, #2a3fae 40%, transparent 75%),
                linear-gradient(135deg, #05071a, #141c55); }
  .photo-wine    { left: 42px;  top: 339px; width: 375px; height: 145px;
    background: radial-gradient(ellipse at 30% 35%, #e8b06a 0%, #9a5a22 35%, transparent 65%),
                linear-gradient(180deg, #2a1208, #5a2e10 60%, #8a5220); }
  .photo-wiring  { left: 438px; top: 339px; width: 349px; height: 145px;
    background: radial-gradient(ellipse at 55% 45%, #e8c080 0%, #a88c6a 30%, transparent 60%),
                linear-gradient(135deg, #3a4a74, #8a94ac 55%, #d6cfc4); }
  .photo-switch  { left: 812px; top: 339px; width: 346px; height: 145px;
    background: radial-gradient(ellipse at 40% 60%, #ffffff 0%, #e6e2dc 40%, transparent 70%),
                linear-gradient(135deg, #d8d2ca, #b8ada2 70%, #8a7e72); }
  .photo-bulb    { left: 42px;  top: 497px; width: 375px; height: 144px;
    background: radial-gradient(ellipse at 40% 45%, #ffffff 0%, #dcdce2 40%, transparent 70%),
                linear-gradient(90deg, #4a3a2c, #8a7a6a 40%, #c8c8cc); }
  .photo-strips  { left: 432px; top: 497px; width: 355px; height: 144px;
    background: radial-gradient(ellipse at 30% 75%, #f4d836 0%, transparent 40%),
                radial-gradient(ellipse at 75% 30%, #f0eee8 0%, transparent 55%),
                linear-gradient(135deg, #c8ccc4, #e8e4d8 50%, #d0a880); }
  .photo-rgb     { left: 812px; top: 497px; width: 346px; height: 144px;
    background: radial-gradient(ellipse at 55% 40%, #e0508a 0%, #7a3aa8 30%, transparent 60%),
                radial-gradient(ellipse at 70% 80%, #e0304a 0%, transparent 40%),
                linear-gradient(135deg, #0e0e14, #1e1e2a); }
  .services {
    position: absolute; left: 42px; top: 662px;
    list-style: none;
    font-family: "Tinos", "Times New Roman", serif;
    font-weight: 700; font-size: 29px; line-height: 37px;
    color: var(--white);
  }
  .contact {
    position: absolute; left: 762px; top: 672px;
    list-style: none;
    font-family: "Tinos", "Times New Roman", serif;
    font-size: 30px; line-height: 52px;
    color: var(--white);
    white-space: nowrap;
  }
  .contact .email { font-size: 24px; }
</style>
</head>
<body>
<main class="flyer">
  <svg class="swoosh" viewBox="0 0 1200 899" aria-hidden="true">
    <path d="M1200 0 L1095 0 C1160 120 1178 300 1170 470 C1164 620 1160 760 1150 899 L1200 899 Z" fill="var(--blue-deep)"/>
    <path d="M1200 0 L1128 0 C1182 140 1194 320 1188 480 C1184 630 1180 760 1176 899 L1200 899 Z" fill="var(--blue-bright)"/>
    <path d="M1144 0 C1188 150 1197 330 1192 490" stroke="var(--blue-light)" stroke-width="6" fill="none"/>
    <path d="M1060 899 C1110 880 1160 870 1200 866 L1200 899 Z" fill="var(--blue-deep)"/>
    <path d="M1110 899 C1150 888 1180 884 1200 882" stroke="var(--blue-light)" stroke-width="4" fill="none"/>
  </svg>

  <div class="brand-mark" aria-hidden="true"></div>
  <h1 class="brand-name">Dirk Malan Electrical</h1>
  <p class="tagline">For All Your Electrical Needs</p>

  <section class="gallery">
    <div class="photo photo-hall" role="img" aria-label="Hallway with blue LED floor lighting"></div>
    <div class="photo photo-kitchen" role="img" aria-label="Timber kitchen with under-cabinet LED lights"></div>
    <div class="photo photo-stairs" role="img" aria-label="Staircase lit by blue LED strip lights"></div>
    <div class="photo photo-wine" role="img" aria-label="Wine rack with warm LED lighting"></div>
    <div class="photo photo-wiring" role="img" aria-label="Hands connecting electrical wiring"></div>
    <div class="photo photo-switch" role="img" aria-label="Screwdriver fitting a wall power point"></div>
    <div class="photo photo-bulb" role="img" aria-label="LED downlight bulb in a dining room"></div>
    <div class="photo photo-strips" role="img" aria-label="Rolls of LED strip lights"></div>
    <div class="photo photo-rgb" role="img" aria-label="Colour-changing RGB LED strip with controller"></div>
  </section>

  <ul class="services">
    <li>Extensions / Renovations</li>
    <li>Safety Switch and Switchboard Upgrades</li>
    <li>LED&nbsp; Lighting Including Downlights</li>
    <li>light fittings and LED strip light</li>
    <li>Re-wires</li>
    <li>Maintenance</li>
  </ul>

  <ul class="contact">
    <li>Tel : &nbsp;- 0437 218 064</li>
    <li>ABN - 41 382 704 916</li>
    <li>REC - 58317</li>
    <li class="email">Email - malanelectrical@brivomail.net</li>
  </ul>
</main>
</body>
</html>
```